Corporate Business Card

Very professional, Modern, Not to busy, include phone address email, website
(253) 617-4930, 18761 52nd Avenue S, Kent, WA 98047, martin@plumlinegroup.com, varkoworks.com

Target Market(s)

Manufacturing

Industry/Entity Type

Aero, machining, manufacturing, Off road racing

Contact Information for Business Card

Phone, address email, website

```html
<!DOCTYPE html>
<html lang="en">
<head>
<meta charset="utf-8">
<title>Varko Works — Business Card</title>
<link href="https://fonts.googleapis.com/css2?family=Open+Sans:wght@400;600;800&display=swap" rel="stylesheet">
<style>
  :root {
    --backdrop: #8a8a88;
    --paper: #ffffff;
    --navy: #16336e;
    --navy-deep: #22366b;
    --navy-soft: #3b5596;
    --red: #d9242b;
    --ink: #3c3c3c;
    --rule: #5a6c96;
  }
  * { margin: 0; padding: 0; box-sizing: border-box; }
  html, body {
    width: 1200px; height: 801px; overflow: hidden;
    background: var(--backdrop);
    font-family: "Open Sans", Arial, sans-serif;
  }
  .stage {
    position: relative; width: 1200px; height: 801px;
    display: flex; align-items: center; justify-content: center; gap: 30px;
  }
  .card {
    position: relative; width: 525px; height: 300px; overflow: hidden;
    box-shadow: 0 10px 24px rgba(0,0,0,.25);
  }
  .card--front { background: var(--paper); }
  .card--back { background: var(--navy-deep); display: flex; align-items: center; justify-content: center; }

  .swoosh { position: absolute; inset: 0; width: 100%; height: 100%; }

  .brand {
    position: absolute; left: 38px; top: 118px; width: 205px;
  }
  .brand__name {
    font-weight: 800; font-size: 34px; letter-spacing: .5px;
    color: var(--navy); line-height: 1;
  }
  .brand__rule { margin-top: 14px; height: 2px; width: 150px; background: var(--navy); }

  .divider {
    position: absolute; left: 262px; top: 92px; width: 1px; height: 92px; background: var(--rule);
  }
  .contact {
    position: absolute; left: 278px; top: 90px;
    font-size: 12.5px; line-height: 18px; color: var(--ink);
  }
  .contact__line { display: flex; align-items: center; gap: 6px; white-space: nowrap; }
  .contact__icon { width: 11px; height: 11px; flex: none; }

  .back-name {
    font-weight: 800; font-size: 56px; letter-spacing: 1px; color: var(--navy-soft);
  }
</style>
</head>
<body>
<main class="stage">
  <section class="card card--front" aria-label="Card front">
    <svg class="swoosh" viewBox="0 0 525 300" preserveAspectRatio="none" aria-hidden="true">
      <path d="M150 300 Q420 255 525 110 L525 300 Z" fill="var(--navy)"/>
      <path d="M235 294 Q445 240 525 92" fill="none" stroke="var(--red)" stroke-width="5"/>
    </svg>

    <div class="brand">
      <div class="brand__name">Varko Works</div>
      <div class="brand__rule"></div>
    </div>

    <div class="divider"></div>

    <div class="contact">
      <div class="contact__line">18761 52nd Avenue S</div>
      <div class="contact__line">Kent, WA 98047</div>
      <div class="contact__line">
        <svg class="contact__icon" viewBox="0 0 12 12" aria-hidden="true"><circle cx="6" cy="6" r="6" fill="var(--red)"/><path d="M4 3.2 L5 4.6 L4.5 5.3 Q5.5 7 6.8 7.5 L7.5 7 L8.8 8 L8 9 Q5 8.6 3.2 4.2 Z" fill="#fff"/></svg>
        (253) 617-4930
      </div>
      <div class="contact__line">
        <svg class="contact__icon" viewBox="0 0 12 12" aria-hidden="true"><circle cx="6" cy="6" r="6" fill="var(--red)"/><rect x="3" y="4" width="6" height="4.2" fill="#fff"/><path d="M3 4 L6 6.4 L9 4" fill="none" stroke="var(--red)" stroke-width=".8"/></svg>
        martin@plumlinegroup.com
      </div>
      <div class="contact__line">
        <svg class="contact__icon" viewBox="0 0 12 12" aria-hidden="true"><circle cx="6" cy="6" r="6" fill="var(--red)"/><circle cx="6" cy="6" r="3" fill="none" stroke="#fff" stroke-width=".9"/><path d="M3 6 H9 M6 3 Q4.5 6 6 9 Q7.5 6 6 3" fill="none" stroke="#fff" stroke-width=".7"/></svg>
        varkoworks.com
      </div>
    </div>
  </section>

  <section class="card card--back" aria-label="Card back">
    <div class="back-name">Varko Works</div>
  </section>
</main>
</body>
</html>
```